Bluecrest Learning Corps by graduating students from college in two years

Based on the logo design, create stationary and business cards for
Dr. Venrel T Oskamp, CEO, (703) 482-1736
and Marisa Deltoft, Respresentative, (301) 647-2208
Address: 4719 Pellham Court, Marlow Ridge, VA 22147
Incorporate elelments of the logo

Target Market(s)

USA

Font styles to use
Other font styles liked:
• match with the logo type style

```html
<!DOCTYPE html>
<html lang="en">
<head>
<meta charset="utf-8">
<title>Bluecrest Learning Corps – Stationery</title>
<link href="https://fonts.googleapis.com/css2?family=Roboto+Condensed:wght@400;700&family=Tinos:ital,wght@0,400;0,700;1,700&display=swap" rel="stylesheet">
<style>
  :root {
    --navy: #1f2a5c;
    --gold: #f8c531;
    --paper: #ffffff;
    --ink: #1b1b1b;
    --ghost: #e4e4ee;
  }
  * { box-sizing: border-box; margin: 0; padding: 0; }
  html, body { width: 1200px; height: 916px; overflow: hidden; }
  body {
    position: relative;
    background: linear-gradient(180deg, #d9dee0, #c8cfd2);
    font-family: "Tinos", "Times New Roman", serif;
    color: var(--navy);
  }
  .sheet { position: absolute; background: var(--paper); overflow: hidden; box-shadow: 0 4px 10px rgba(0,0,0,.18); }

  /* business cards */
  .card { left: 68px; width: 437px; height: 249px; }
  .card--front { top: 66px; background: var(--gold); }
  .card--ceo { top: 339px; }
  .card--rep { top: 614px; }

  .wordmark { position: absolute; display: flex; align-items: center; gap: 6px; font-weight: 700; color: var(--navy); white-space: nowrap; }
  .wordmark__dot { flex: none; border-radius: 50%; background: var(--navy); }
  .card--front .wordmark { left: 0; right: 0; top: 112px; justify-content: center; font-size: 22px; }
  .card--front .wordmark__dot { width: 18px; height: 18px; }
  .card .wordmark--small { left: 14px; top: 56px; font-size: 13px; }
  .card .wordmark--small .wordmark__dot { width: 12px; height: 12px; background: var(--gold); }

  .ghost-cap { position: absolute; background: radial-gradient(ellipse at center, var(--ghost) 0%, rgba(228,228,238,.55) 70%, rgba(228,228,238,0) 100%); }
  .card .ghost-cap { left: 221px; top: 55px; width: 216px; height: 140px; }

  .card__name { position: absolute; right: 18px; top: 100px; font-weight: 700; font-size: 19px; color: var(--gold); letter-spacing: .5px; white-space: nowrap; }
  .card__role { position: absolute; right: 18px; top: 126px; font-size: 11px; color: var(--navy); }
  .card__tab { position: absolute; right: 0; top: 109px; width: 12px; height: 31px; background: var(--gold); }

  .card__address { position: absolute; left: 15px; top: 132px; font-size: 11.5px; line-height: 15px; }
  .contact { list-style: none; position: absolute; font-size: 11.5px; }
  .contact li { display: flex; align-items: center; height: 15px; gap: 6px; white-space: nowrap; }
  .contact svg { width: 9px; height: 9px; flex: none; }
  .card .contact { left: 15px; top: 174px; }

  .swoosh { position: absolute; left: 0; bottom: 0; display: block; }

  /* letterhead */
  .letterhead { left: 562px; top: 66px; width: 558px; height: 787px; }
  .letterhead .wordmark--small { left: 29px; top: 62px; font-size: 14px; }
  .letterhead .wordmark--small .wordmark__dot { width: 14px; height: 14px; background: var(--gold); }
  .letterhead__contact { list-style: none; position: absolute; right: 20px; top: 42px; font-size: 12.5px; text-align: right; }
  .letterhead__contact li { display: flex; justify-content: flex-end; align-items: center; gap: 10px; height: 16px; white-space: nowrap; }
  .letterhead__contact svg { width: 10px; height: 10px; }
  .rule { position: absolute; top: 122px; height: 3px; }
  .rule--navy { left: 29px; width: 230px; height: 1.5px; top: 123px; background: var(--navy); }
  .rule--gold { left: 259px; width: 270px; background: var(--gold); }

  .letterhead .ghost-cap { left: 87px; top: 278px; width: 368px; height: 188px; }

  .person { position: absolute; font-family: "Roboto Condensed", "Arial Narrow", sans-serif; font-size: 28px; line-height: 1; color: var(--navy); white-space: nowrap; }
  .person b { color: var(--gold); font-weight: 700; }
  .person__role { position: absolute; font-size: 11px; color: var(--ink); }
  .sender { left: 29px; top: 195px; }
  .sender-role { left: 30px; top: 224px; }
  .date { position: absolute; right: 42px; top: 204px; font-size: 13px; color: var(--ink); }
  .letterhead .contact { left: 29px; top: 252px; color: var(--ink); font-size: 11px; }
  .letterhead .contact li { height: 13px; gap: 6px; }

  .letter-body { position: absolute; left: 29px; width: 498px; top: 316px; font-size: 12px; line-height: 16px; color: var(--ink); text-align: justify; }
  .letter-body p + p { margin-top: 16px; }

  .signature { position: absolute; left: 29px; top: 591px; width: 189px; height: 60px; background: linear-gradient(90deg, #eeeeef, #e2e2e6); border-radius: 4px; }
  .signer { left: 29px; top: 654px; }
  .signer-role { left: 30px; top: 684px; }

  .label { position: absolute; font-style: italic; font-weight: 700; font-size: 32px; color: #f4f5f6; text-shadow: 0 2px 3px rgba(0,0,0,.35); white-space: nowrap; }
  .label--cards { left: 143px; top: 868px; }
  .label--letter { left: 727px; top: 860px; }
</style>
</head>
<body>

<svg width="0" height="0" style="position:absolute" aria-hidden="true">
  <symbol id="i-phone" viewBox="0 0 10 10"><path d="M2 .8 3.6 2.6 2.8 3.7C3.4 5 4.8 6.4 6.2 7.1L7.3 6.3 9.2 8 8.2 9.3C4.6 9 1 5.4.7 1.8Z" fill="#f8c531"/></symbol>
  <symbol id="i-globe" viewBox="0 0 10 10"><circle cx="5" cy="5" r="4.3" fill="none" stroke="#f8c531" stroke-width="1.1"/><path d="M.8 5h8.4M5 .7c-2.3 2.6-2.3 6 0 8.6M5 .7c2.3 2.6 2.3 6 0 8.6" fill="none" stroke="#f8c531" stroke-width=".9"/></symbol>
  <symbol id="i-mail" viewBox="0 0 10 10"><rect x=".7" y="2" width="8.6" height="6.2" rx=".6" fill="none" stroke="#f8c531" stroke-width="1.1"/><path d="M.9 2.3 5 5.6 9.1 2.3" fill="none" stroke="#f8c531" stroke-width="1"/></symbol>
  <symbol id="i-pin" viewBox="0 0 10 10"><path d="M5 9.6C3 7 1.8 5.3 1.8 3.6a3.2 3.2 0 0 1 6.4 0C8.2 5.3 7 7 5 9.6Z" fill="none" stroke="#f8c531" stroke-width="1.1"/><circle cx="5" cy="3.6" r="1.2" fill="#f8c531"/></symbol>
</svg>

<!-- Business card: front -->
<section class="sheet card card--front">
  <div class="wordmark"><span class="wordmark__dot"></span>Bluecrest Learning Corps</div>
</section>

<!-- Business card: CEO -->
<section class="sheet card card--ceo">
  <div class="wordmark wordmark--small"><span class="wordmark__dot"></span>Bluecrest Learning Corps</div>
  <div class="ghost-cap" role="img" aria-label="Faint graduation cap decoration"></div>
  <div class="card__name">Dr. Venrel T Oskamp</div>
  <div class="card__role">CEO</div>
  <div class="card__tab"></div>
  <p class="card__address">4719 Pellham Court,<br>Marlow Ridge, VA 22147</p>
  <ul class="contact">
    <li><svg><use href="#i-phone"/></svg>(703) 482-1736</li>
    <li><svg><use href="#i-globe"/></svg>www.bluecrestcorps.org</li>
    <li><svg><use href="#i-mail"/></svg>hello@bluecrestcorps.org</li>
  </ul>
  <svg class="swoosh" width="437" height="40" viewBox="0 0 437 40">
    <path d="M0 40V35C120 10 260 0 372 6 250 4 160 20 92 40Z" fill="#f8c531"/>
    <path d="M94 40C190 18 310 6 437 36V40Z" fill="#1f2a5c"/>
  </svg>
</section>

<!-- Business card: representative -->
<section class="sheet card card--rep">
  <div class="wordmark wordmark--small"><span class="wordmark__dot"></span>Bluecrest Learning Corps</div>
  <div class="ghost-cap" role="img" aria-label="Faint graduation cap decoration"></div>
  <div class="card__name">Marisa Deltoft</div>
  <div class="card__role">Respresentative</div>
  <div class="card__tab"></div>
  <p class="card__address">4719 Pellham Court,<br>Marlow Ridge, VA 22147</p>
  <ul class="contact">
    <li><svg><use href="#i-phone"/></svg>(301) 647-2208</li>
    <li><svg><use href="#i-globe"/></svg>www.bluecrestcorps.org</li>
    <li><svg><use href="#i-mail"/></svg>hello@bluecrestcorps.org</li>
  </ul>
  <svg class="swoosh" width="437" height="40" viewBox="0 0 437 40">
    <path d="M0 40V35C120 10 260 0 372 6 250 4 160 20 92 40Z" fill="#f8c531"/>
    <path d="M94 40C190 18 310 6 437 36V40Z" fill="#1f2a5c"/>
  </svg>
</section>

<!-- A4 letterhead -->
<section class="sheet letterhead">
  <div class="wordmark wordmark--small"><span class="wordmark__dot"></span>Bluecrest Learning Corps</div>
  <ul class="letterhead__contact">
    <li>(703) 482-1736<svg><use href="#i-phone"/></svg></li>
    <li>www.bluecrestcorps.org<svg><use href="#i-globe"/></svg></li>
    <li>hello@bluecrestcorps.org<svg><use href="#i-mail"/></svg></li>
    <li>4719 Pellham Court, Marlow Ridge, VA 22147<svg><use href="#i-pin"/></svg></li>
  </ul>
  <div class="rule rule--navy"></div>
  <div class="rule rule--gold"></div>

  <div class="ghost-cap" role="img" aria-label="Faint graduation cap decoration"></div>

  <div class="person sender"><b>Tesska</b> Marvold</div>
  <div class="person__role sender-role">Founder &amp; CEO</div>
  <div class="date">August-05-2019</div>
  <ul class="contact">
    <li><svg><use href="#i-phone"/></svg>(817) 350-4192</li>
    <li><svg><use href="#i-globe"/></svg>www.bluecrestcorps.org</li>
    <li><svg><use href="#i-mail"/></svg>hello@bluecrestcorps.org</li>
  </ul>

  <div class="letter-body">
    <p>Lorem ipsum dolor sit amet, consectetuer adipiscing elit, sed diam nonummy nibh euismod tincidunt ut laoreet dolore magna aliquam erat volutpat. Ut wisi enim ad minim veniam, quis nostrud exerci tation ullamcorper suscipit lobortis</p>
    <p>Lorem ipsum dolor sit amet, cons ectetuer adipiscing elit, sed diam nonummy nibh euismod tincidunt ut laoreet dolore magna aliquam erat volutpat. Ut wisi enim ad minim veniam, quis nostrud exerci tation ullamcorper suscipit lobortis nisl ut aliquip ex ea commodo consequat. Lorem ipsum dolor sit amet, consectetuer olutpat. Ut wisi enim ad minim veniam, quis nostrud exerci tation ullamcorper suscipit lobortis nisl ut aliquip ex ea commodo consequat. Duis autem</p>
    <p>vel eum iriure dolor in hendrerit in vulputate velit esse molestie consequat, vel illum dolore eu feugiat nulla facilisis at vero eros et accumsan et iusto odio dignissim qui blandit praesent luptatum zzril delenit augue duis dolore te feugait nulla facilisi. Lorem ipsum dolor sit amet, cons ectetuer adipiscing elit, sed diam nonummy nibh euismod tincidunt ut laoreet dolore magna aliquam erat volutpat. Ut wisi enim .</p>
  </div>

  <div class="signature" role="img" aria-label="Handwritten signature of the director"></div>
  <div class="person signer"><b>Brenna</b> Kolvatri</div>
  <div class="person__role signer-role">Director</div>

  <svg class="swoosh" width="558" height="34" viewBox="0 0 558 34">
    <path d="M0 34V30C140 8 320 -2 475 6 340 4 240 14 135 34Z" fill="#f8c531"/>
    <path d="M135 34C250 14 400 4 558 32V34Z" fill="#1f2a5c"/>
  </svg>
</section>

<div class="label label--cards">Business card</div>
<div class="label label--letter">A4 Letterhead</div>

</body>
</html>
```